KDWB Business Card

Looking for a business card design to incorporate our branding. We want to only use the colors listing in the Branding Package (attached).
Updates

Target Market(s)

People who need their phone or device fixed.

Industry/Entity Type

Electronics

Contact Information for Business Card

Please use:

Brightwick Gadget Clinic LLC
4810 E Harlow Ridge Rd
Suite 417
San Antonio, TX 78163

Marcus Delgrove, Store Manager

(210) 555-0147

Requirements
Must have
• Must include the colors that are contained within the Branding Package PDF file.

```html
<!DOCTYPE html>
<html lang="en">
<head>
<meta charset="utf-8">
<title>Brightwick Gadget Clinic – Business Card</title>
<link rel="stylesheet" href="https://fonts.googleapis.com/css2?family=Questrial&display=swap">
<style>
  :root {
    --canvas-bg: #ecebe8;
    --card-white: #fbfbfb;
    --brand-orange: #e2521f;
    --brand-orange-deep: #cf4519;
    --brand-orange-soft: #f26a2c;
    --text-grey: #8c8c8c;
    --frame-light: #f3d6c8;
  }
  * { box-sizing: border-box; margin: 0; padding: 0; }
  html, body { width: 1200px; height: 625px; overflow: hidden; }
  body {
    background: var(--canvas-bg);
    font-family: "Questrial", "Century Gothic", sans-serif;
    display: flex;
    align-items: center;
    justify-content: center;
    gap: 60px;
  }
  .card {
    position: relative;
    width: 504px;
    height: 288px;
    border-radius: 22px;
    box-shadow: 0 10px 26px rgba(0,0,0,0.14);
  }
  .card-frame {
    position: absolute;
    inset: 14px;
    border-radius: 16px;
    border: 1.5px solid var(--brand-orange);
  }
  .card--front { background: linear-gradient(160deg, #ffffff, var(--card-white) 60%, #f0f0f0); }
  .card--back { background: linear-gradient(160deg, var(--brand-orange-soft), var(--brand-orange) 45%, var(--brand-orange-deep)); }
  .card--back .card-frame { border-color: var(--frame-light); }

  .brand {
    display: flex;
    align-items: center;
    gap: 10px;
  }
  .brand-mark {
    width: 30px;
    height: 30px;
    border-radius: 6px;
    background: var(--brand-orange);
    flex: none;
  }
  .brand-name {
    font-size: 21px;
    line-height: 1;
    color: var(--brand-orange);
    white-space: nowrap;
  }
  .card--back .brand-mark { background: #ffffff; }
  .card--back .brand-name { color: #ffffff; }

  .card--front .brand { position: absolute; left: 42px; bottom: 46px; }
  .card--back .brand {
    position: absolute;
    left: 50%;
    top: 50%;
    transform: translate(-50%, -50%);
  }
  .card--back .brand-name { font-size: 24px; }
  .card--back .brand-mark { width: 34px; height: 34px; }

  .contact {
    position: absolute;
    left: 258px;
    top: 42px;
    color: var(--text-grey);
    font-size: 13px;
    line-height: 1.55;
  }
  .contact-name {
    color: var(--brand-orange);
    font-size: 21px;
    font-weight: 400;
    line-height: 1.2;
  }
  .contact-role { margin-bottom: 14px; font-size: 14px; }
  .contact-address { font-style: normal; margin-bottom: 6px; }
  .contact-phone-label { color: var(--brand-orange); }
</style>
</head>
<body>
  <section class="card card--front" aria-label="Business card front">
    <div class="card-frame"></div>
    <div class="contact">
      <h1 class="contact-name">Marcus Delgrove</h1>
      <p class="contact-role">Store Manager</p>
      <address class="contact-address">
        4810 E Harlow Ridge Rd<br>
        Suite 417<br>
        San Antonio, TX 78163
      </address>
      <p class="contact-phone"><span class="contact-phone-label">Phone:</span> (210) 555-0147</p>
    </div>
    <div class="brand">
      <span class="brand-mark"></span>
      <span class="brand-name">Brightwick Gadget Clinic</span>
    </div>
  </section>

  <section class="card card--back" aria-label="Business card back">
    <div class="card-frame"></div>
    <div class="brand">
      <span class="brand-mark"></span>
      <span class="brand-name">Brightwick Gadget Clinic</span>
    </div>
  </section>
</body>
</html>
```